Web Design for an Innovative Life Science Marketplace

IMPORTANT:
The software is called CS-Cart. It has capabilities and limitations with design features in the software. There is a certain framework that needs to be followed. It is PHP and Linux. It may require add-ons for your design, so please be specific with what is required. It’s preferred the designer has CS-Cart knowledge/experience.

Key Requirements
1. I’d like the design to include an implemented/recommended CS-Cart theme that is consistent with our branding (see the marketing collateral and logo).
2. I then need the additional design changes to that theme to create the below web pages.
3. All designs should be consistent with our branding. All pictures should either be computer generated (clip art-like) or pictures of happy patients. What is a happy patient? Close up photo of someone healthy, happy, and experiencing/enjoying life. Not someone in a hospital or getting care. Please see examples already on the site.

Please see the attached Web Design details in the word document. That document is important to complete the design.

```html
<!DOCTYPE html>
<html lang="en">
<head>
<meta charset="utf-8">
<title>Loopsource — Life Science Marketplace</title>
<link href="https://fonts.googleapis.com/css2?family=Oswald:wght@400;500;600&family=Open+Sans:wght@400;600;700&display=swap" rel="stylesheet">
<style>
:root{
  --green:#8dc63f;
  --green-dark:#79b12e;
  --teal:#0f8a78;
  --ink:#222;
  --dark:#333;
  --darker:#1b1b1b;
  --muted:#666;
  --line:#e2e2e2;
  --pale:#eaf2f5;
  --white:#fff;
}
*{box-sizing:border-box;margin:0;padding:0}
html,body{width:1200px;height:3965px;overflow:hidden}
body{font-family:"Open Sans",Arial,sans-serif;color:var(--ink);background:var(--white);font-size:13px}
.heading{font-family:"Oswald","Arial Narrow",sans-serif;text-transform:uppercase;font-weight:500}
.wrap{position:relative;width:858px;margin:0 auto;height:100%}
section,header,footer,nav{position:relative}

.topbar{height:35px;background:var(--dark);color:#ddd;font-size:11px}
.topbar .wrap{display:flex;align-items:center;gap:26px}
.topbar span{display:flex;align-items:center;gap:7px}
.topbar .account{margin-left:auto}

.masthead{height:115px}
.brand{position:absolute;left:0;top:28px;display:flex;align-items:center;gap:10px;font-family:"Oswald",sans-serif;font-weight:600;font-size:26px;color:var(--green);letter-spacing:.5px}
.brand i{display:block;width:34px;height:34px;border-radius:50%;background:var(--teal)}
.search{position:absolute;left:298px;top:40px;display:flex}
.search input{width:270px;height:34px;border:1px solid var(--line);padding:0 12px;font:12px "Open Sans",sans-serif}
.search button{width:75px;height:34px;border:0;background:var(--green);display:flex;align-items:center;justify-content:center}
.cart{position:absolute;left:716px;top:34px;display:flex;gap:12px;align-items:center;white-space:nowrap}
.cart i{flex:none;width:38px;height:38px;border-radius:50%;background:var(--green);display:flex;align-items:center;justify-content:center}
.cart b{display:block;font-weight:600;font-size:14px}
.cart small{font-size:11px;color:var(--muted)}

.mainnav{height:43px;border-top:1px solid var(--line);border-bottom:1px solid var(--line);z-index:2}
.mainnav ul{list-style:none;display:flex;height:43px;align-items:center;gap:38px;font-size:12px;font-weight:600;color:#444}
.register{position:absolute;right:0;top:-8px;height:59px;width:172px;background:var(--green);color:#fff;display:flex;align-items:center;justify-content:center;gap:10px;font-family:"Oswald",sans-serif;font-size:16px;letter-spacing:.5px}
.register i{width:24px;height:24px;border-radius:50%;background:#fff}

.ph{display:block}
.hero{height:523px;background:linear-gradient(120deg,#8fb85a 0%,#c8dca8 40%,#f3f1ec 60%,#7aa34a 100%)}

.split{height:262px;display:flex}
.split .left{width:590px;background:#3a3a3a;color:#fff;padding:52px 0 0 172px}
.split .left p{font-size:11px;line-height:16px;width:380px;color:#ddd}
.split .left h2{font-size:25px;margin:22px 0 26px;letter-spacing:.5px}
.btn-outline{display:inline-block;border:2px solid #fff;color:#fff;font:600 12px "Oswald",sans-serif;text-transform:uppercase;padding:10px 30px;letter-spacing:.5px}
.split .right{flex:1;background:var(--teal);color:#fff;padding:52px 160px 0 40px}
.split .right h3{font-size:19px;line-height:34px;letter-spacing:.5px}

.block-head{text-align:center}
.block-head h2{font-size:30px;color:#111;letter-spacing:.5px}
.block-head svg{display:block;margin:6px auto 18px}
.block-head p{font-size:11px;line-height:17px;color:#444}

.join{height:462px;padding-top:46px}
.cards{display:flex;gap:24px;margin-top:40px}
.card{width:270px;height:213px;border:1px solid var(--line);text-align:center;padding-top:22px}
.card .icon{width:58px;height:58px;border-radius:50%;border:2px solid var(--teal);margin:0 auto;display:flex;align-items:center;justify-content:center}
.card h4{font-family:"Oswald",sans-serif;font-weight:500;font-size:14px;margin:18px 0 10px;color:#222}
.card p{font-size:11px;line-height:17px;color:#444;padding:0 38px}
.products .card{height:272px}
.btn-green{display:inline-block;margin-top:26px;background:var(--green);color:#fff;font:600 12px "Oswald",sans-serif;padding:9px 20px;letter-spacing:.5px}

.about{height:326px;background:var(--green);color:#fff}
.about h2{position:absolute;left:0;top:42px;font-size:31px}
.about p{position:absolute;left:0;top:102px;width:480px;font-size:11px;line-height:17px}
.about .btn-outline{position:absolute;left:0;top:232px;padding:8px 24px;font-size:11px}
.about .frame{position:absolute;left:528px;top:54px;width:350px;height:220px;border:6px solid #fff;background:var(--white)}
.about .frame .ph{width:100%;height:100%;background:linear-gradient(135deg,#e8eef2,#c9d6de 60%,#b7a48e)}

.products{height:539px;padding-top:46px}

.marketing{height:346px;display:flex}
.marketing .ph{width:612px;height:100%;background:linear-gradient(110deg,#f3d340 0%,#e7e3dc 45%,#c9b8a6 100%)}
.marketing .copy{flex:1;background:var(--teal);color:#fff;padding:52px 40px 0 38px}
.marketing h2{font-size:31px;letter-spacing:.5px}
.marketing p{font-size:11px;line-height:17px;margin:18px 0 28px;width:390px}
.marketing .btn-outline{font:400 14px "Open Sans",sans-serif;text-transform:none;padding:9px 16px;margin-right:16px}

.statement{height:346px;display:flex}
.statement .copy{width:612px;background:#242424;color:#fff;display:flex;align-items:center;justify-content:center;text-align:center}
.statement h2{font-size:25px;line-height:40px;letter-spacing:.5px}
.statement .ph{flex:1;background:linear-gradient(135deg,#ececec,#9ea3a8 60%,#5c6166)}

.promise{height:505px;padding-top:60px}
.promise-box{position:absolute;left:0;top:212px;width:858px;height:232px;display:flex}
.promise-box .text{width:513px;border:1px solid var(--line);border-right:0;display:flex;align-items:center;justify-content:center;text-align:center;padding:0 30px}
.promise-box h3{font-size:25px;line-height:34px;color:#222;letter-spacing:.5px;font-weight:500}
.promise-box .ph{flex:1;background:linear-gradient(120deg,#eef3f6,#bcd3e3 50%,#5a8fc2)}

.newsletter{height:140px;background:var(--pale)}
.newsletter h2{position:absolute;left:0;top:40px;font-size:22px;color:#111}
.newsletter .rule{position:absolute;left:165px;top:53px;width:80px;height:2px;background:var(--green)}
.newsletter p{position:absolute;left:0;top:80px;font-size:11px;color:#333}
.newsletter form{position:absolute;left:484px;top:52px;display:flex}
.newsletter input{width:282px;height:44px;border:2px solid var(--green);background:transparent;padding:0 18px;font:12px "Open Sans",sans-serif;color:#666}
.newsletter button{width:102px;height:44px;border:0;background:var(--green);color:#fff;font:600 13px "Oswald",sans-serif}

.footer{height:323px;background:var(--darker);color:#ddd}
.footer .links{display:flex;gap:50px;font-size:11px;padding-top:24px;height:60px;border-bottom:1px solid #333}
.footer .cols{position:absolute;top:86px;left:0;width:858px}
.footer .col{position:absolute;top:0}
.footer h5{font-family:"Oswald",sans-serif;font-weight:500;font-size:13px;color:#fff;margin-bottom:16px}
.footer li{list-style:none;font-size:11px;line-height:15px}
.footer .contact li{display:flex;gap:10px;margin-bottom:14px}
.social{display:flex;gap:10px}
.social span{width:24px;height:24px;border:1px solid #ccc;border-radius:50%}
.copyright{position:absolute;left:0;right:0;top:270px;border-top:1px solid #333;padding-top:16px;font-size:11px}
</style>
</head>
<body>

<div class="topbar">
  <div class="wrap">
    <span><svg width="12" height="9" viewBox="0 0 12 9"><rect x=".5" y=".5" width="11" height="8" fill="none" stroke="#ccc"/><path d="M.5 .5l5.5 4.5 5.5-4.5" fill="none" stroke="#ccc"/></svg>hello@loopsource-mkt.com</span>
    <span><svg width="10" height="10" viewBox="0 0 10 10"><path d="M2 0l2 2-1 2 3 3 2-1 2 2-2 2C4 10 0 6 0 2z" fill="#ccc"/></svg>+1 800-555-0142</span>
    <span class="account"><svg width="10" height="10" viewBox="0 0 10 10"><circle cx="5" cy="3" r="2.5" fill="#ccc"/><path d="M0 10c0-3 2-4.5 5-4.5s5 1.5 5 4.5z" fill="#ccc"/></svg>My Account</span>
  </div>
</div>

<header class="masthead">
  <div class="wrap">
    <div class="brand"><i></i>LOOPSOURCE</div>
    <form class="search"><input type="text" placeholder="Search Products..."><button type="button"><svg width="14" height="14" viewBox="0 0 14 14"><circle cx="6" cy="6" r="4.5" fill="none" stroke="#fff" stroke-width="2"/><path d="M9.5 9.5l3.5 3.5" stroke="#fff" stroke-width="2"/></svg></button></form>
    <div class="cart"><i><svg width="16" height="14" viewBox="0 0 16 14"><path d="M0 1h3l2 8h8l2-6H4" fill="none" stroke="#fff" stroke-width="1.6"/><circle cx="6" cy="12" r="1.3" fill="#fff"/><circle cx="12" cy="12" r="1.3" fill="#fff"/></svg></i><div><b>Shopping Cart</b><small>item(s) - $0.00</small></div></div>
  </div>
</header>

<nav class="mainnav">
  <div class="wrap">
    <ul><li>HOME</li><li>ABOUT US</li><li>HOW IT WORKS</li><li>WHY LOOPSOURCE</li><li>FAQ</li><li>CONTACT US</li></ul>
    <div class="register"><i></i>REGISTRATION</div>
  </div>
</nav>

<section class="hero ph" role="img" aria-label="Close-up photo of a happy, healthy woman relaxing outdoors among green leaves"></section>

<section class="split">
  <div class="left">
    <p>Lorem Ipsum is simply dummy text of the printing and typesetting industry. Lorem Ipsum has been the industry's standard.</p>
    <h2 class="heading">Join the Circular Supply Chain</h2>
    <span class="btn-outline">Pre-Register</span>
  </div>
  <div class="right">
    <h3 class="heading">A virtual multi-vendor marketplace and for the life sciences community to connect and transact before and after-market materials and equipment</h3>
  </div>
</section>

<section class="join">
  <div class="wrap">
    <div class="block-head">
      <h2 class="heading">Who Should Join</h2>
      <svg width="100" height="8" viewBox="0 0 100 8"><path d="M2 5Q50 0 98 5" fill="none" stroke="var(--green)" stroke-width="2"/></svg>
      <p>Lorem Ipsum is simply dummy text of the printing and typesetting industry. Lorem Ipsum has been the industry's standard<br>Lorem Ipsum is simply dummy text of the printing and typesetting industry.</p>
    </div>
    <div class="cards">
      <div class="card"><div class="icon"><svg width="28" height="22" viewBox="0 0 28 22"><path d="M2 20V10l7-4v4l7-4v4l7-4v14z" fill="none" stroke="var(--teal)" stroke-width="2"/></svg></div><h4>MANUFACTURERS</h4><p>Create an Account in Minutes to Sell/Buy Excess or Obsolete Materials and Equipment</p></div>
      <div class="card"><div class="icon"><svg width="26" height="26" viewBox="0 0 26 26"><circle cx="11" cy="11" r="7" fill="none" stroke="var(--teal)" stroke-width="2"/><path d="M16 16l7 7" stroke="var(--teal)" stroke-width="2.5"/></svg></div><h4>RESEARCHERS</h4><p>Sell/Buy Low-Cost Materials and Receive Donations</p></div>
      <div class="card"><div class="icon"><svg width="24" height="28" viewBox="0 0 24 28"><circle cx="7" cy="5" r="3" fill="none" stroke="var(--teal)" stroke-width="2"/><circle cx="17" cy="5" r="3" fill="none" stroke="var(--teal)" stroke-width="2"/><path d="M3 26V12h8v14M13 26V12h8v14" fill="none" stroke="var(--teal)" stroke-width="2"/></svg></div><h4>ORIGINAL SUPPLIERS</h4><p>Market Your Products Across a Broad Life Sciences Network</p></div>
    </div>
  </div>
</section>

<section class="about">
  <div class="wrap">
    <h2 class="heading">About Us</h2>
    <p>Lorem Ipsum is simply dummy text of the printing and typesetting industry. Lorem Ipsum has been the industry's standard. Lorem Ipsum is simply dummy text of the printing and typesetting industry. Lorem Ipsum has been the industry's standard. Lorem Ipsum is simply dummy text of the printing and typesetting industry. Lorem Ipsum has been the industry's standard.</p>
    <span class="btn-outline">Read More</span>
    <div class="frame"><div class="ph" role="img" aria-label="Photo of a smiling, healthy older couple enjoying time together"></div></div>
  </div>
</section>

<section class="products">
  <div class="wrap">
    <div class="block-head">
      <h2 class="heading">Products</h2>
      <svg width="100" height="8" viewBox="0 0 100 8"><path d="M2 5Q50 0 98 5" fill="none" stroke="var(--green)" stroke-width="2"/></svg>
      <p>Lorem Ipsum is simply dummy text of the printing and typesetting industry. Lorem Ipsum has been the industry's standard<br>Lorem Ipsum is simply dummy text of the printing and typesetting industry.</p>
    </div>
    <div class="cards">
      <div class="card"><div class="icon"><svg width="22" height="26" viewBox="0 0 22 26"><rect x="3" y="2" width="16" height="22" fill="none" stroke="var(--teal)" stroke-width="2"/><path d="M7 9h8M7 14h8M7 19h5" stroke="var(--teal)" stroke-width="2"/></svg></div><h4>RAW MATERIALS</h4><p>Consumable and starting materials for API and intermediate manufacturing or research</p><span class="btn-green">VIEW DETAILS</span></div>
      <div class="card"><div class="icon"><svg width="26" height="26" viewBox="0 0 26 26"><circle cx="13" cy="13" r="5" fill="none" stroke="var(--teal)" stroke-width="2"/><circle cx="13" cy="13" r="10" fill="none" stroke="var(--teal)" stroke-width="2" stroke-dasharray="4 3"/></svg></div><h4>EQUIPMENT</h4><p>e.g. End item systems manufactured for LS applications</p><span class="btn-green">VIEW DETAILS</span></div>
      <div class="card"><div class="icon"><svg width="26" height="26" viewBox="0 0 26 26"><path d="M13 3v20M3 13h20M6 6l14 14M20 6L6 20" stroke="var(--teal)" stroke-width="2"/></svg></div><h4>PARTS</h4><p>e.g. Components of a modular system used for LS applications</p><span class="btn-green">VIEW DETAILS</span></div>
    </div>
  </div>
</section>

<section class="marketing">
  <div class="ph" role="img" aria-label="Photo of a smiling young woman holding a small model in a bright room"></div>
  <div class="copy">
    <h2 class="heading">Marketing Materials</h2>
    <p>Lorem Ipsum than two centuries of craftsmanship and a perpetual commitment to perfection. There is no mystery about a Suit He simply more than two centuries of craftsmanship and a perpetual commitment to perfection Lorem Ipsum.</p>
    <span class="btn-outline">Read Our White Paper</span><span class="btn-outline">Read Our Brochure</span>
  </div>
</section>

<section class="statement">
  <div class="copy"><h2 class="heading">Lorem Ipsum is simply dummy text of<br>the printing and typesetting industry<br>Lorem Ipsum has been the</h2></div>
  <div class="ph" role="img" aria-label="Photo of hands using a tablet and phone on a desk beside a laptop"></div>
</section>

<section class="promise">
  <div class="wrap">
    <div class="block-head">
      <h2 class="heading">Our Promise</h2>
      <svg width="100" height="8" viewBox="0 0 100 8"><path d="M2 5Q50 0 98 5" fill="none" stroke="var(--green)" stroke-width="2"/></svg>
      <p>Lorem Ipsum is simply dummy text of the printing and typesetting industry. Lorem Ipsum has been the industry's standard<br>Lorem Ipsum is simply dummy text of the printing and typesetting industry.</p>
    </div>
    <div class="promise-box">
      <div class="text"><h3 class="heading">A greener, more cost-efficient, and quality-driven supply chain through a collaborative life sciences marketplace</h3></div>
      <div class="ph" role="img" aria-label="Photo of a cheerful caregiver in blue scrubs with an older man"></div>
    </div>
  </div>
</section>

<section class="newsletter">
  <div class="wrap">
    <h2 class="heading">Get the Latest</h2>
    <span class="rule"></span>
    <p>SIGN UP FOR OUR NEWSLETTER TO GET THE LATEST ON ALL THINGS SUPPLY</p>
    <form><input type="email" placeholder="YOUR MAIL"><button type="button">JOIN NOW</button></form>
  </div>
</section>

<footer class="footer">
  <div class="wrap">
    <div class="links"><span>HOME</span><span>ABOUT US</span><span>HOW IT WORKS</span><span>WHY LOOPSOURCE</span></div>
    <div class="cols">
      <div class="col contact" style="left:0">
        <h5>CONTACT US</h5>
        <ul>
          <li><svg width="10" height="13" viewBox="0 0 10 13"><path d="M5 0a5 5 0 0 1 5 5c0 3-5 8-5 8S0 8 0 5a5 5 0 0 1 5-5z" fill="#ddd"/></svg><span>48 Harbor Lane Suite 5, Westfield,<br><br>OH 44000</span></li>
          <li><svg width="10" height="10" viewBox="0 0 10 10"><path d="M2 0l2 2-1 2 3 3 2-1 2 2-2 2C4 10 0 6 0 2z" fill="#ddd"/></svg>+1 800-555-0142</li>
          <li><svg width="12" height="9" viewBox="0 0 12 9"><rect x=".5" y=".5" width="11" height="8" fill="none" stroke="#ddd"/><path d="M.5 .5l5.5 4.5 5.5-4.5" fill="none" stroke="#ddd"/></svg>hello@loopsource-mkt.com</li>
        </ul>
      </div>
      <div class="col" style="left:294px"><h5>CUSTOMER SERVICE</h5><ul><li>My Account</li><li>Contact Us</li><li>Site Map</li><li>Terms of Service</li><li>Privacy Policy</li></ul></div>
      <div class="col" style="left:500px"><h5>COMPANY INFO</h5><ul><li>About us</li><li>FAQ</li><li>Contact Us</li></ul></div>
      <div class="col" style="left:692px"><h5>SOCIAL LINK</h5><div class="social"><span></span><span></span><span></span><span></span></div></div>
    </div>
    <div class="copyright">© 2018 Loopsource . All Rights Reserved.</div>
  </div>
</footer>

</body>
</html>
```